Automotive Business Card Design

I would just like a automotive themed card. nothing too extravagant, but catchy.

needs to say something about doing roadside assistance,mobile repairs, Diesel repairs, and Fleet maintenance

it can be single sided or double sided. no preference there.

Industry/Entity Type

Automotive

Contact Information for Business Card

Dean Marlowe
phone 534 861 2093
Name: Brightpath Automotive & Diesel Repair

```html
<!DOCTYPE html>
<html lang="en">
<head>
<meta charset="utf-8">
<title>Dean Marlowe – Business Card</title>
<link href="https://fonts.googleapis.com/css2?family=Jost:wght@400;500;700&display=swap" rel="stylesheet">
<style>
  :root {
    --page-bg: #2b2b2d;
    --card-light: #ffffff;
    --card-shade: #d9d9db;
    --ink: #111111;
    --ink-soft: #2a2a2a;
    --accent-red: #c4161c;
    --car-light: #f2f2f3;
    --car-mid: #b9babd;
    --car-dark: #6f7073;
  }
  * { margin: 0; padding: 0; box-sizing: border-box; }
  html, body {
    width: 1200px;
    height: 900px;
    overflow: hidden;
    background: var(--page-bg);
    font-family: "Jost", "Futura", sans-serif;
  }
  .business-card {
    position: absolute;
    left: 100px;
    top: 164px;
    width: 1000px;
    height: 572px;
    border-radius: 30px;
    overflow: hidden;
    background: linear-gradient(200deg, var(--card-light) 0%, #f3f3f4 45%, var(--card-shade) 100%);
  }
  .car-visual {
    position: absolute;
    right: 0;
    top: 40px;
    width: 540px;
    height: 440px;
    border-radius: 200px 0 0 60px;
    background: radial-gradient(ellipse at 55% 45%, var(--car-light) 0%, var(--car-mid) 55%, var(--car-dark) 100%);
    opacity: 0.9;
  }
  .greeting {
    position: absolute;
    left: 70px;
    top: 150px;
  }
  .greeting-intro {
    font-size: 36px;
    font-weight: 400;
    color: var(--ink);
    letter-spacing: 1px;
    line-height: 1;
  }
  .owner-name {
    margin-top: 8px;
    font-size: 44px;
    font-weight: 700;
    color: var(--accent-red);
    letter-spacing: 1px;
    line-height: 1;
  }
  .phone-line {
    margin-top: 10px;
    display: flex;
    align-items: center;
    gap: 16px;
    font-size: 46px;
    font-weight: 400;
    color: var(--ink);
    line-height: 1;
  }
  .phone-icon { width: 50px; height: 40px; }
  .service-list {
    position: absolute;
    left: 70px;
    top: 370px;
    list-style: none;
  }
  .service-item {
    position: relative;
    padding-left: 20px;
    margin-bottom: 22px;
    font-size: 27px;
    font-weight: 400;
    color: var(--ink-soft);
    line-height: 1.1;
    letter-spacing: 0.5px;
  }
  .service-item::before {
    content: "";
    position: absolute;
    left: 0;
    top: 4px;
    bottom: 4px;
    width: 6px;
    background: var(--accent-red);
  }
</style>
</head>
<body>
  <div class="business-card">
    <div class="car-visual" role="img" aria-label="Photo of a silver sedan seen from the rear three-quarter view"></div>

    <div class="greeting">
      <p class="greeting-intro">HI, I’M</p>
      <p class="owner-name">DEAN MARLOWE</p>
      <p class="phone-line">
        <svg class="phone-icon" viewBox="0 0 50 40" aria-hidden="true">
          <path d="M3 14 Q25 -2 47 14 L47 18 L37 18 L36 12 Q25 8 14 12 L13 18 L3 18 Z" fill="var(--accent-red)"/>
          <path d="M12 20 L38 20 L44 36 L6 36 Z" fill="var(--accent-red)"/>
          <g fill="#ffffff">
            <circle cx="19" cy="25" r="1.8"/><circle cx="25" cy="25" r="1.8"/><circle cx="31" cy="25" r="1.8"/>
            <circle cx="17" cy="31" r="1.8"/><circle cx="25" cy="31" r="1.8"/><circle cx="33" cy="31" r="1.8"/>
          </g>
        </svg>
        <span>534 861 2093</span>
      </p>
    </div>

    <ul class="service-list">
      <li class="service-item">Roadside Assistance,</li>
      <li class="service-item">Mobile Repairs,</li>
      <li class="service-item">Diesel Repairs<br>&amp; Fleet Maintenance</li>
    </ul>
  </div>
</body>
</html>
```